Harbor Loom Floors Letterhead

Letterhead used for business reasons. It must be editable and easy to use.

Address is 2715 W. Pelican Lane Englewood FL 34187 - 941.382.6519

```html
<!DOCTYPE html>
<html lang="en">
<head>
<meta charset="utf-8">
<title>Harbor Loom Floors Letterhead</title>
<link href="https://fonts.googleapis.com/css2?family=Lato:wght@400;700&family=Montserrat:wght@400&family=Tangerine:wght@700&display=swap" rel="stylesheet">
<style>
  :root {
    --backdrop: #e2e2e2;
    --paper: #ffffff;
    --band: #1a1a1a;
    --accent: #e08b2b;
    --ink: #1c1c1c;
    --header-text: #f2f2f2;
  }
  * { margin: 0; padding: 0; box-sizing: border-box; }
  html, body {
    width: 1174px;
    height: 1200px;
    overflow: hidden;
    background: var(--backdrop);
  }
  .letterhead {
    position: absolute;
    left: 138px;
    top: 20px;
    width: 897px;
    height: 1160px;
    background: var(--paper);
    box-shadow: 0 2px 10px rgba(0,0,0,0.18);
    font-family: "Lato", sans-serif;
    color: var(--ink);
  }
  .masthead {
    position: absolute;
    left: 0; top: 0;
    width: 100%;
    height: 234px;
    background: var(--band);
  }
  .brand-name {
    position: absolute;
    left: 56px;
    top: 62px;
    font-family: "Montserrat", sans-serif;
    font-weight: 400;
    font-size: 38px;
    line-height: 46px;
    color: var(--accent);
  }
  .contact {
    position: absolute;
    left: 646px;
    top: 88px;
    height: 64px;
    padding-left: 26px;
    border-left: 2px solid var(--accent);
    font-family: "Montserrat", sans-serif;
    font-size: 15px;
    line-height: 21px;
    color: var(--header-text);
  }
  .contact-address { margin-top: -3px; }
  .contact-phone {
    display: flex;
    align-items: center;
    gap: 5px;
    margin-top: 10px;
  }
  .contact-phone svg { width: 13px; height: 13px; }
  .letter-body {
    position: absolute;
    left: 56px;
    width: 785px;
  }
  .letter-date { top: 284px; font-size: 18px; }
  .recipient { top: 327px; font-size: 17px; line-height: 20px; }
  .recipient-company { top: 406px; font-size: 17px; line-height: 21px; }
  .salutation { top: 507px; font-size: 21px; font-weight: 700; }
  .paragraph {
    font-size: 16.5px;
    line-height: 19.5px;
    text-align: justify;
  }
  .p1 { top: 574px; }
  .p2 { top: 670px; }
  .p3 { top: 768px; }
  .p4 { top: 845px; }
  .closing { top: 925px; font-size: 17px; }
  .signature {
    top: 1008px;
    font-family: "Tangerine", cursive;
    font-weight: 700;
    font-size: 48px;
  }
</style>
</head>
<body>
  <main class="letterhead">
    <header class="masthead">
      <div class="brand-name">Harbor Loom<br>Floors</div>
      <div class="contact">
        <p class="contact-address">2715 W. Pelican Lane<br>Englewood FL 34187</p>
        <p class="contact-phone">
          <svg viewBox="0 0 24 24" aria-hidden="true"><path fill="var(--accent)" d="M6.6 10.8a15.1 15.1 0 0 0 6.6 6.6l2.2-2.2a1 1 0 0 1 1-.25 11.4 11.4 0 0 0 3.6.57 1 1 0 0 1 1 1V20a1 1 0 0 1-1 1A17 17 0 0 1 3 4a1 1 0 0 1 1-1h3.5a1 1 0 0 1 1 1c0 1.25.2 2.45.57 3.57a1 1 0 0 1-.25 1z"/></svg>
          941.382.6519
        </p>
      </div>
    </header>

    <p class="letter-body letter-date">January-03-2020</p>
    <p class="letter-body recipient">Mr, Alan Whitford<br>President</p>
    <p class="letter-body recipient-company">Crestline Corporation<br>123 Street Name, Suite# 10<br>City, State, 120023</p>
    <p class="letter-body salutation">Dear Mr, Alan</p>

    <p class="letter-body paragraph p1">Lorem ipsum dolor sit amet, consectetur adipiscing elit, sed do eiusmod tempor incididunt ut labore et dolore magna aliqua. Ut enim ad minim veniam, quis nostrud exercitation ullamco laboris nisi ut aliquip ex ea commodo consequat. Duis aute irure dolor in reprehenderit in voluptate velit esse cillum dolore eu fugiat nulla pariatur.</p>
    <p class="letter-body paragraph p2">Lorem ipsum dolor sit amet, consectetur adipiscing elit, sed do eiusmod tempor incididunt ut labore et dolore magna aliqua. Ut enim ad minim veniam, quis nostrud exercitation ullamco laboris nisi ut aliquip ex ea commodo consequat. Duis aute irure dolor in reprehenderit in voluptate velit esse cillum dolore eu fugiat nulla pariatur.</p>
    <p class="letter-body paragraph p3">Lorem ipsum dolor sit amet, consectetur adipiscing elit, sed do eiusmod tempor incididunt ut labore et dolore magna aliqua. Ut enim ad minim veniam, quis nostrud exercitation ullamco laboris nisi ut aliquip ex ea commodo consequat.</p>
    <p class="letter-body paragraph p4">Excepteur sint occaecat cupidatat non proident, sunt in culpa qui officia deserunt mollit anim id est laborum. re et dolore magnam aliquam quaerat voluptatem.</p>

    <p class="letter-body closing">Regards</p>
    <p class="letter-body signature">Daniel Marsh</p>
  </main>
</body>
</html>
```